Non Profit raising scholarship funds needs flyer for Golf Tournament

We need a flyer for our upcoming golf tournament. Proceeds to will help to benefit our Harwell Bridging Futures Scholarship Fund.

Title: 2019 B-RovMT Golf Tournament
Location: KRV San Antonio
Date: May 15, 2019
Registration: $175 individual, $700 foursome
Sponsorships starting at $250
Benefiting B-RovMT and the Harwell Bridging Futures Scholarship Fund

Target Market(s)

Design and Construction industry professionals

Industry/Entity Type

Construction

Font styles to use
Serif
Sans Serif

Colors

Designer to choose colors to be used in the design.

Requirements
Must have
• Title, date, location, registration info, sponsor info, benefit info, logo
Nice to have
• I like the retro look of some golf flyers, but it's not necessary
Should not have
• .

```html
<!DOCTYPE html>
<html lang="en">
<head>
<meta charset="UTF-8">
<title>2019 B-RovMT Golf Tournament</title>
<link rel="stylesheet" href="https://fonts.googleapis.com/css2?family=Saira+Condensed:wght@600;700&family=Quicksand:wght@600;700&family=Open+Sans:wght@700&display=swap">
<style>
  :root {
    --canvas: #e0e0e0;
    --paper: #fbfafa;
    --green: #6a8f2e;
    --green-light: #8ab543;
    --green-text: #5e8a24;
    --olive-top: #737d2c;
    --olive-bottom: #5c6e22;
    --olive-fold: #3f5a1e;
    --charcoal: #434343;
    --ink: #2b2b2b;
    --footer: #111111;
    --logo-blue: #2f4a9c;
    --sky-top: #7fbdf0;
    --sky-low: #bfe0f6;
    --grass: #5fa72f;
    --grass-deep: #3f8a25;
  }
  * { box-sizing: border-box; margin: 0; padding: 0; }
  html, body { width: 1200px; height: 1200px; overflow: hidden; background: var(--canvas); }
  .canvas { position: relative; width: 1200px; height: 1200px; }
  .flyer {
    position: absolute; left: 190px; top: 25px;
    width: 710px; height: 996px;
    transform: scale(1.155); transform-origin: top left;
    background: var(--paper); overflow: hidden;
  }
  .flyer-shapes { position: absolute; inset: 0; }
  .brand {
    position: absolute; left: 505px; top: 30px; width: 200px;
    display: flex; flex-direction: column; align-items: center; gap: 10px;
  }
  .brand-dot { width: 62px; height: 62px; border-radius: 50%; background: var(--logo-blue); }
  .brand-name { font-family: "Quicksand", sans-serif; font-weight: 600; font-size: 34px; color: var(--charcoal); line-height: 1; }
  .title {
    position: absolute; left: 150px; top: 410px; width: 410px;
    font-family: "Saira Condensed", sans-serif; font-weight: 700;
    color: #fff; text-align: center; font-size: 50px; line-height: 72px;
    text-transform: uppercase; letter-spacing: 1px;
  }
  .date {
    position: absolute; left: 0; width: 710px; top: 598px; text-align: center;
    font-family: "Saira Condensed", sans-serif; font-weight: 700;
    font-size: 80px; line-height: 90px; color: var(--green-text); letter-spacing: 2px;
  }
  .location { position: absolute; left: 0; top: 705px; width: 333px; }
  .location-head {
    background: var(--charcoal); color: #fff; height: 58px;
    font-family: "Quicksand", sans-serif; font-weight: 700; font-size: 50px; line-height: 58px;
    padding-left: 50px;
  }
  .location-body {
    height: 61px; border: 1.5px solid var(--ink); border-left: none; background: #fff;
    font-family: "Quicksand", sans-serif; font-weight: 700; font-size: 30px; line-height: 56px;
    color: var(--ink); text-align: center;
  }
  .registration { position: absolute; left: 408px; top: 705px; width: 239px; border-collapse: collapse; }
  .registration th {
    background: var(--charcoal); color: #fff; height: 42px;
    font-family: "Quicksand", sans-serif; font-weight: 700; font-size: 33px; line-height: 38px;
    border: 1.5px solid var(--ink);
  }
  .registration td {
    height: 46px; border: 1.5px solid var(--ink);
    font-family: "Quicksand", sans-serif; font-weight: 700; font-size: 26px; color: var(--ink);
    padding-left: 12px; background: #fff;
  }
  .registration td.price { background: var(--green); color: #fff; width: 87px; padding-left: 9px; }
  .sponsors {
    position: absolute; left: 0; width: 710px; top: 860px; text-align: center;
    font-family: "Saira Condensed", sans-serif; font-weight: 700; text-transform: uppercase;
    color: var(--ink); font-size: 28px; line-height: 44px;
  }
  .sponsors .accent { color: var(--green-text); }
  .sponsors .lead { font-size: 40px; letter-spacing: 1px; }
  .benefit {
    position: absolute; left: 0; width: 710px; top: 914px; text-align: center;
    font-family: "Open Sans", sans-serif; font-weight: 700; font-size: 15.5px; color: var(--ink);
  }
  .benefit .accent { color: var(--green-text); }
  .footer-band { position: absolute; left: 0; bottom: 0; width: 710px; height: 36px; background: var(--footer); }
</style>
</head>
<body>
<div class="canvas">
  <div class="flyer">
    <svg class="flyer-shapes" width="710" height="996" viewBox="0 0 710 996" xmlns="http://www.w3.org/2000/svg">
      <defs>
        <linearGradient id="photoTone" x1="0" y1="0" x2="0" y2="1">
          <stop offset="0" stop-color="var(--sky-top)"/>
          <stop offset="0.22" stop-color="var(--sky-low)"/>
          <stop offset="0.3" stop-color="var(--grass)"/>
          <stop offset="1" stop-color="var(--grass-deep)"/>
        </linearGradient>
        <linearGradient id="bannerTone" x1="0" y1="0" x2="0" y2="1">
          <stop offset="0" stop-color="var(--olive-top)"/>
          <stop offset="1" stop-color="var(--olive-bottom)"/>
        </linearGradient>
      </defs>
      <rect x="0" y="0" width="710" height="570" fill="url(#photoTone)" role="img" aria-label="Photo of golfers on a sunny fairway, one mid-swing while two watch"/>
      <path d="M457 0 Q470 205 710 220 V0 Z" fill="var(--paper)"/>
      <polygon points="0,328 150,468 0,553" fill="var(--green)"/>
      <polygon points="710,293 540,553 710,636" fill="var(--green)"/>
      <polygon points="0,553 165,526 540,553 710,636 710,996 0,996" fill="var(--paper)"/>
      <polygon points="0,553 160,505 170,528" fill="var(--green-light)"/>
      <polygon points="110,436 140,400 150,470" fill="var(--olive-fold)"/>
      <polygon points="135,390 575,390 540,581 175,581" fill="url(#bannerTone)"/>
    </svg>

    <div class="brand">
      <div class="brand-dot"></div>
      <div class="brand-name">B-RovMT</div>
    </div>

    <h1 class="title">2019 B-RovMT<br>Golf Tournament</h1>
    <p class="date">May 15, 2019</p>

    <div class="location">
      <div class="location-head">Location</div>
      <div class="location-body">KRV San Antonio</div>
    </div>

    <table class="registration">
      <tr><th colspan="2">Registration</th></tr>
      <tr><td class="price">$175</td><td>Individual</td></tr>
      <tr><td class="price">$700</td><td>Foursome</td></tr>
    </table>

    <p class="sponsors"><span class="accent lead">Sponsorships</span> starting at <span class="accent lead">$250</span></p>
    <p class="benefit"><span class="accent">Benefiting B-</span>RovMT and the Harwell Bridging Futures Scholarship Fund</p>

    <div class="footer-band"></div>
  </div>
</div>
</body>
</html>
```